Bramblewood Card Company Business Cards

We are a trading card store with Glimmorax, sports and other TCG cards, we need a business card design that encompasses a clean cut, modern style with a retro flare. website is bramblewoodcardco.com for reference. Can utilize a comic book era feel or a more modern outdoor feel to utilize the "Pacific Northwest" elements of tress, mountains, etc.

Industry/Entity Type

Trading cards and collectibles

Contact Information for Business Card

business name, email address, phone number, name, owner job title

Font styles to use
Sans Serif

```html
<!DOCTYPE html>
<html lang="en">
<head>
<meta charset="utf-8">
<title>Bramblewood Card Company — Business Cards</title>
<link rel="stylesheet" href="https://fonts.googleapis.com/css2?family=Montserrat:wght@400;500;800&display=swap">
<style>
  :root {
    --backdrop: #1c1c1c;
    --card-grey: #858585;
    --card-grey-dark: #797979;
    --brand-blue: #26c0e2;
    --paper-white: #ffffff;
    --ink-white: #f4f4f4;
  }
  * { box-sizing: border-box; margin: 0; padding: 0; }
  html, body {
    width: 1200px; height: 900px; overflow: hidden;
    background: var(--backdrop);
    font-family: "Montserrat", Arial, sans-serif;
  }
  .sheet {
    width: 1200px; height: 900px;
    display: flex; flex-direction: column;
    align-items: center; justify-content: center; gap: 36px;
  }
  .card {
    width: 700px; height: 400px;
    background: linear-gradient(135deg, var(--card-grey-dark), var(--card-grey));
    position: relative;
    box-shadow: 0 10px 24px rgba(0,0,0,.5);
  }
  /* Front */
  .card--front {
    display: flex; align-items: center; justify-content: center;
  }
  .brand-mark {
    display: flex; align-items: center; gap: 14px;
    color: var(--paper-white);
    font-weight: 800; text-transform: uppercase;
    letter-spacing: 1px; line-height: 1.05;
  }
  .brand-mark__dot {
    width: 22px; height: 22px; border-radius: 50%;
    background: var(--brand-blue); flex: none;
  }
  .card--front .brand-mark { font-size: 30px; }
  /* Back */
  .card--back { display: flex; align-items: center; }
  .card--back .brand-zone {
    width: 330px; display: flex; justify-content: center;
  }
  .card--back .brand-mark { font-size: 24px; }
  .divider {
    width: 2px; height: 230px; background: var(--brand-blue);
  }
  .contact {
    padding-left: 42px; color: var(--ink-white);
  }
  .contact__name {
    font-weight: 800; font-size: 34px; letter-spacing: 2px;
    color: var(--brand-blue); text-transform: uppercase; line-height: 1;
  }
  .contact__title {
    font-weight: 500; font-size: 15px; letter-spacing: 1.5px;
    text-transform: uppercase; margin-top: 4px;
  }
  .contact__address {
    margin-top: 22px; font-size: 15px; line-height: 1.35; letter-spacing: .5px;
  }
  .contact__list { list-style: none; margin-top: 22px; }
  .contact__item {
    display: flex; align-items: center; gap: 12px;
    font-size: 16px; letter-spacing: .5px; margin-bottom: 8px;
  }
  .contact__icon { width: 16px; height: 16px; flex: none; }
</style>
</head>
<body>
<main class="sheet">
  <section class="card card--front" aria-label="Business card front">
    <div class="brand-mark">
      <span class="brand-mark__dot"></span>
      <span>Bramblewood<br>Card Company</span>
    </div>
  </section>

  <section class="card card--back" aria-label="Business card back">
    <div class="brand-zone">
      <div class="brand-mark">
        <span class="brand-mark__dot"></span>
        <span>Bramblewood<br>Card Company</span>
      </div>
    </div>
    <div class="divider"></div>
    <div class="contact">
      <h1 class="contact__name">Dalen Marsh</h1>
      <p class="contact__title">Manager</p>
      <p class="contact__address">482 Alder Ridge Lane<br>Your Country, MN 46210</p>
      <ul class="contact__list">
        <li class="contact__item">
          <svg class="contact__icon" viewBox="0 0 24 24" aria-hidden="true"><path fill="var(--brand-blue)" d="M6.6 10.8a15 15 0 0 0 6.6 6.6l2.2-2.2a1 1 0 0 1 1-.25 11.4 11.4 0 0 0 3.6.57 1 1 0 0 1 1 1V20a1 1 0 0 1-1 1A17 17 0 0 1 3 4a1 1 0 0 1 1-1h3.5a1 1 0 0 1 1 1c0 1.25.2 2.45.57 3.57a1 1 0 0 1-.25 1z"/></svg>
          <span>(312)555-0147</span>
        </li>
        <li class="contact__item">
          <svg class="contact__icon" viewBox="0 0 24 24" aria-hidden="true"><path fill="var(--brand-blue)" d="M2 5h20v14H2z"/><path fill="none" stroke="#7f7f7f" stroke-width="1.6" d="M2 5l10 8 10-8"/></svg>
          <span>hello@bramblewoodcardco.com</span>
        </li>
        <li class="contact__item">
          <svg class="contact__icon" viewBox="0 0 24 24" aria-hidden="true"><g fill="none" stroke="var(--brand-blue)" stroke-width="2"><circle cx="12" cy="12" r="10"/><ellipse cx="12" cy="12" rx="4.5" ry="10"/><path d="M2 12h20M4 7h16M4 17h16"/></g></svg>
          <span>www.bramblewoodcardco.com</span>
        </li>
      </ul>
    </div>
  </section>
</main>
</body>
</html>
```